Military and tactical gear supply company needs web design

We need a web design for a company called U.S. Torvane. We provide quality tactical equipment to military and law enforcement. This is an e-commerce business and we primarily market ourselves on social media. Our key products are backpacks, military-style belts, and tactical flashlights. The gear we sell is not yet widely known about, but is on par with the state-of-the-art products in this field. We want the website to convey the message of quality, durability, and reliability. We use the word "kinetic" because the customers in this field are very "action-oriented" and we would like that idea to be communicated in the web site as well. The primary demographic is men in their 20's-30's, so the web site should have a masculine feel to it. Attached is the logo and color scheme.

```html
<!DOCTYPE html>
<html lang="en">
<head>
<meta charset="utf-8">
<title>U.S. Torvane — Tactical Gear</title>
<link rel="stylesheet" href="https://fonts.googleapis.com/css2?family=Montserrat:ital,wght@0,400;0,500;0,600;0,700;1,400&family=Open+Sans:wght@400;600;700&display=swap">
<style>
:root{
  --navy:#2b4d68;
  --topbar:#27516e;
  --red:#b0131f;
  --ink:#222;
  --muted:#8a8a8a;
  --light:#efefef;
  --footer:#232323;
  --bottom:#141414;
  --white:#fff;
}
*{margin:0;padding:0;box-sizing:border-box}
html,body{width:1200px;height:3976px;overflow:hidden}
body{position:relative;font-family:"Open Sans",sans-serif;color:var(--ink);background:var(--white)}
.abs{position:absolute}
.topbar{left:0;top:0;width:1200px;height:37px;background:var(--topbar);color:var(--white);font-size:15px;text-align:center;line-height:37px}
.contact-mail{left:120px;top:47px;font-size:13px;color:#333;display:flex;align-items:center;gap:5px}
.search{left:527px;top:38px;width:268px;height:36px;border:1px solid #ccc;font-size:12px;color:#999;padding:10px 10px}
.search-btn{left:795px;top:38px;width:43px;height:36px;background:var(--red);display:flex;align-items:center;justify-content:center}
.account{left:838px;top:38px;width:250px;height:36px;background:#1e1e1e;color:var(--white);font-size:12px;display:flex;align-items:center;justify-content:flex-end;gap:20px;padding-right:18px}
.brand{left:116px;top:93px;font-family:"Montserrat",sans-serif;font-weight:700;font-size:30px;color:var(--navy);letter-spacing:1px;line-height:38px}
.nav{left:0;top:100px;width:1200px;height:44px}
.nav a{position:absolute;top:4px;font-size:15px;color:#222;text-decoration:none;font-family:"Open Sans",sans-serif}
.nav a.active{color:var(--red)}
.nav .bar{position:absolute;left:576px;top:40px;width:52px;height:3px;background:var(--red)}
.hero{left:0;top:144px;width:1200px;height:557px;background:linear-gradient(90deg,#6b6346 0%,#8a7f5f 20%,#4d4a3c 38%,#1a1a1e 55%,#0c0c12 100%)}
.hero-mark{left:615px;top:280px;width:473px;text-align:right;font-family:"Montserrat",sans-serif;font-weight:700;font-size:56px;color:var(--white);letter-spacing:2px}
.hero-text{left:560px;top:377px;width:528px;text-align:right;font-family:"Montserrat",sans-serif;font-size:16px;line-height:26px;color:var(--white)}
.shop{left:903px;top:460px;width:185px;height:56px}
.section-title{width:1200px;left:0;text-align:center;font-family:"Montserrat",sans-serif;font-weight:500;font-size:26px;color:#222}
.rule{left:547px;width:108px;height:2px;background:var(--red)}
.card{width:227px;height:272px;border:1px solid #cfcfcf;background:var(--white)}
.card .photo{position:absolute;left:30px;top:15px;width:165px;height:155px;border-radius:6px}
.card p{position:absolute;left:12px;top:193px;width:203px;font-size:8px;line-height:11px;color:#555;text-align:center}
.card .price{position:absolute;left:-1px;bottom:-1px;width:227px;height:39px;background:var(--navy);color:var(--white);font-size:17px;display:flex;align-items:center;justify-content:space-between;padding:0 16px 0 45px}
.about{left:0;top:1553px;width:1200px;height:451px;background:linear-gradient(135deg,#2f5372 0%,#284963 45%,#335877 100%)}
.about h2{position:absolute;left:0;top:90px;width:1200px;text-align:center;font-family:"Montserrat",sans-serif;font-weight:500;font-size:26px;color:var(--white)}
.about .lead{position:absolute;left:225px;top:153px;width:750px;text-align:center;font-family:"Montserrat",sans-serif;font-weight:600;font-size:16px;line-height:26px;color:var(--white)}
.about .body{position:absolute;left:225px;top:229px;width:750px;text-align:center;font-size:15px;line-height:26px;color:#e6ecf2}
.feature{left:145px;width:420px}
.feature h3{position:absolute;left:55px;top:0;font-family:"Montserrat",sans-serif;font-weight:500;font-size:27px;color:#222}
.feature p{position:absolute;left:57px;top:40px;width:360px;font-size:13px;line-height:26px;color:var(--muted)}
.feature svg{position:absolute;left:0;top:4px}
.feature-photo{left:608px;top:2098px;width:488px;height:338px;background:linear-gradient(160deg,#5a4632 0%,#3a2d22 45%,#1d1a17 100%)}
.reviews{left:0;top:2532px;width:1200px;height:371px;background:var(--light)}
.reviews h2{position:absolute;left:0;top:84px;width:1200px;text-align:center;font-family:"Montserrat",sans-serif;font-weight:500;font-size:27px;color:#222}
.reviews .rule2{position:absolute;left:547px;top:128px;width:108px;height:2px;background:var(--red)}
.reviews blockquote{position:absolute;left:210px;top:160px;width:780px;text-align:center;font-family:"Montserrat",sans-serif;font-style:italic;font-size:16px;line-height:26px;color:#555}
.arrow{position:absolute;top:191px;width:26px;height:47px;background:#555;display:flex;align-items:center;justify-content:center}
.blog-main{left:122px;top:3071px;width:482px;height:298px;background:linear-gradient(160deg,#2b3138 0%,#1c2126 55%,#111417 100%)}
.blog-main-title{left:130px;top:3383px;width:470px;font-family:"Montserrat",sans-serif;font-weight:600;font-size:17px;line-height:26px;color:#222}
.blog-main-text{left:130px;top:3446px;width:470px;font-size:16px;line-height:26px;color:var(--muted)}
.blog-thumb{left:614px;width:170px;height:143px}
.blog-item{left:805px;width:290px;font-family:"Montserrat",sans-serif;font-weight:600;font-size:17px;line-height:26px;color:#222}
.footer{left:0;top:3617px;width:1200px;height:280px;background:var(--footer);color:var(--white)}
.footer .fbrand{position:absolute;left:136px;top:108px;font-family:"Montserrat",sans-serif;font-weight:700;font-size:26px;color:var(--white);letter-spacing:1px}
.social{position:absolute;top:168px;width:30px;height:30px;border-radius:50%}
.footer h4{position:absolute;top:60px;font-family:"Montserrat",sans-serif;font-weight:600;font-size:26px;color:var(--white)}
.ci{position:absolute;left:478px;width:240px;font-family:"Montserrat",sans-serif;font-size:15px;line-height:26px;color:#ddd}
.ci svg{position:absolute;left:0;top:7px}
.ci span{display:block;padding-left:26px}
.news-input{position:absolute;left:804px;top:112px;width:283px;height:49px;background:var(--white);border:1px solid #ccc;color:#888;font-size:12px;padding:16px 12px}
.subscribe{position:absolute;left:810px;top:189px;width:118px;height:43px;background:var(--red);color:var(--white);font-family:"Montserrat",sans-serif;font-weight:700;font-size:16px;display:flex;align-items:center;justify-content:center}
.bottom{left:0;top:3897px;width:1200px;height:79px;background:var(--bottom);color:#eee;font-size:11px;text-align:center;line-height:79px}
</style>
</head>
<body>

<div class="abs topbar">Lorem ipsum dolor sit amet, consectetur adipiscing elit</div>

<div class="abs contact-mail">
  <svg width="12" height="10" viewBox="0 0 12 10"><rect x="0.5" y="0.5" width="11" height="9" fill="#333"/><path d="M0.5 0.5 L6 5 L11.5 0.5" stroke="#fff" fill="none"/></svg>
  info@ustorvane.com
</div>
<div class="abs search">Search</div>
<div class="abs search-btn"><svg width="14" height="14" viewBox="0 0 14 14"><circle cx="6" cy="6" r="4" stroke="#fff" stroke-width="2" fill="none"/><line x1="9" y1="9" x2="12.5" y2="12.5" stroke="#fff" stroke-width="2"/></svg></div>
<div class="abs account"><span>&#9679; Account</span><span>Cart</span><span>0 items</span></div>

<div class="abs brand">U.S. TORVANE</div>
<nav class="abs nav">
  <a class="active" style="left:580px">Home</a>
  <a style="left:658px">About Us</a>
  <a style="left:757px">Products</a>
  <a style="left:854px">Catalog</a>
  <a style="left:942px">Blog</a>
  <a style="left:1007px">Contact Us</a>
  <span class="bar"></span>
</nav>

<section class="abs hero" role="img" aria-label="Soldier in full tactical gear and helmet amid smoke on a dark background"></section>
<div class="abs hero-mark">U.S. TORVANE</div>
<p class="abs hero-text">Lorem ipsum dolor sit amet, consectetur adipiscing elit, sed do<br>eiusmod tempor incid et dolore magna aliqua.</p>
<svg class="abs shop" viewBox="0 0 185 56"><polygon points="20,0 185,0 165,56 0,56" fill="#b0131f"/><text x="92" y="35" text-anchor="middle" font-family="Montserrat,sans-serif" font-weight="700" font-size="17" fill="#fff">SHOP NOW</text></svg>

<h2 class="abs section-title" style="top:786px">OUR FEATURED PRODUCTS</h2>
<div class="abs rule" style="top:838px"></div>

<div class="abs card" style="left:111px;top:886px"><div class="photo" role="img" aria-label="Olive tactical backpack" style="background:#e9ebe4"></div><p>Lorem ipsum dolor sit amet, consectetur adipiscing elit, sed do eiusmod tempor</p><div class="price">$ 150.00<svg width="14" height="12" viewBox="0 0 14 12"><path d="M0 1h3l2 7h7l2-5H4" fill="#fff"/><circle cx="6" cy="10.5" r="1.3" fill="#fff"/><circle cx="11" cy="10.5" r="1.3" fill="#fff"/></svg></div></div>
<div class="abs card" style="left:361px;top:886px"><div class="photo" role="img" aria-label="Green military belt" style="background:#eaede2"></div><p>Lorem ipsum dolor sit amet, consectetur adipiscing elit, sed do eiusmod tempor</p><div class="price">$ 150.00<svg width="14" height="12" viewBox="0 0 14 12"><path d="M0 1h3l2 7h7l2-5H4" fill="#fff"/><circle cx="6" cy="10.5" r="1.3" fill="#fff"/><circle cx="11" cy="10.5" r="1.3" fill="#fff"/></svg></div></div>
<div class="abs card" style="left:611px;top:886px"><div class="photo" role="img" aria-label="Black tactical flashlight with lanyard" style="background:#eeeeee"></div><p>Lorem ipsum dolor sit amet, consectetur adipiscing elit, sed do eiusmod tempor</p><div class="price">$ 150.00<svg width="14" height="12" viewBox="0 0 14 12"><path d="M0 1h3l2 7h7l2-5H4" fill="#fff"/><circle cx="6" cy="10.5" r="1.3" fill="#fff"/><circle cx="11" cy="10.5" r="1.3" fill="#fff"/></svg></div></div>
<div class="abs card" style="left:862px;top:886px"><div class="photo" role="img" aria-label="Camouflage pack with boots and folded gear" style="background:#e8e5da"></div><p>Lorem ipsum dolor sit amet, consectetur adipiscing elit, sed do eiusmod tempor</p><div class="price">$ 150.00<svg width="14" height="12" viewBox="0 0 14 12"><path d="M0 1h3l2 7h7l2-5H4" fill="#fff"/><circle cx="6" cy="10.5" r="1.3" fill="#fff"/><circle cx="11" cy="10.5" r="1.3" fill="#fff"/></svg></div></div>

<div class="abs card" style="left:111px;top:1186px"><div class="photo" role="img" aria-label="Compact black flashlight" style="background:#eeeeee"></div><p>Lorem ipsum dolor sit amet, consectetur adipiscing elit, sed do eiusmod tempor</p><div class="price">$ 150.00<svg width="14" height="12" viewBox="0 0 14 12"><path d="M0 1h3l2 7h7l2-5H4" fill="#fff"/><circle cx="6" cy="10.5" r="1.3" fill="#fff"/><circle cx="11" cy="10.5" r="1.3" fill="#fff"/></svg></div></div>
<div class="abs card" style="left:361px;top:1186px"><div class="photo" role="img" aria-label="Olive duffel bag" style="background:#eae9e2"></div><p>Lorem ipsum dolor sit amet, consectetur adipiscing elit, sed do eiusmod tempor</p><div class="price">$ 150.00<svg width="14" height="12" viewBox="0 0 14 12"><path d="M0 1h3l2 7h7l2-5H4" fill="#fff"/><circle cx="6" cy="10.5" r="1.3" fill="#fff"/><circle cx="11" cy="10.5" r="1.3" fill="#fff"/></svg></div></div>
<div class="abs card" style="left:611px;top:1186px"><div class="photo" role="img" aria-label="Angle-head military flashlight" style="background:#ebece6"></div><p>Lorem ipsum dolor sit amet, consectetur adipiscing elit, sed do eiusmod tempor</p><div class="price">$ 150.00<svg width="14" height="12" viewBox="0 0 14 12"><path d="M0 1h3l2 7h7l2-5H4" fill="#fff"/><circle cx="6" cy="10.5" r="1.3" fill="#fff"/><circle cx="11" cy="10.5" r="1.3" fill="#fff"/></svg></div></div>
<div class="abs card" style="left:862px;top:1186px"><div class="photo" role="img" aria-label="Set of tactical belts with buckles" style="background:#e9e8e1"></div><p>Lorem ipsum dolor sit amet, consectetur adipiscing elit, sed do eiusmod tempor</p><div class="price">$ 150.00<svg width="14" height="12" viewBox="0 0 14 12"><path d="M0 1h3l2 7h7l2-5H4" fill="#fff"/><circle cx="6" cy="10.5" r="1.3" fill="#fff"/><circle cx="11" cy="10.5" r="1.3" fill="#fff"/></svg></div></div>

<section class="abs about" role="img" aria-label="Blue-tinted soldier with rifle in the background">
  <h2>ABOUT US</h2>
  <p class="lead">Lorem ipsum dolor sit amet, consectetur adipiscing elit, sed do eiusmod tempor incididunt ut labore et dolore magna aliqua. Ut enim ad minim veniam.</p>
  <p class="body">Duis aute irure dolor in reprehenderit in voluptate velit esse cillum dolore eu fugiat nulla pariatur. Excepteur sint occaecat cupidatat non proident, sunt in culpa qui officia deserunt mollit anim id est laborum.Lorem ipsum dolor sit amet, consectetur adipiscing elit, sed do eiusmod tempor incididunt ut labore et dolore magna aliqua. Ut enim ad minim veniam, quis nostrud exercitation ullamco laboris nisi ut aliquip ex ea commodo consequat.</p>
</section>

<div class="abs feature" style="top:2112px">
  <svg width="38" height="38" viewBox="0 0 38 38" fill="none" stroke="#222" stroke-width="2"><rect x="3" y="16" width="8" height="18"/><path d="M11 18 L18 8 Q20 3 23 6 L21 15 H32 Q35 16 34 20 L31 31 Q30 34 27 34 H11"/></svg>
  <h3>Quality</h3>
  <p>Lorem ipsum dolor sit amet, consectetur adipiscing elit, sed do eiusmod tempor incididunt ut</p>
</div>
<div class="abs feature" style="top:2215px">
  <svg width="40" height="38" viewBox="0 0 40 38" fill="none" stroke="#222" stroke-width="2"><path d="M6 26 L24 6 L30 12 L12 30 Z"/><line x1="2" y1="33" x2="38" y2="33"/><line x1="2" y1="37" x2="38" y2="37" stroke="#b0131f"/></svg>
  <h3>Durability</h3>
  <p>Lorem ipsum dolor sit amet, consectetur adipiscing elit, sed do eiusmod tempor incididunt ut</p>
</div>
<div class="abs feature" style="top:2317px">
  <svg width="38" height="38" viewBox="0 0 38 38" fill="none" stroke="#222" stroke-width="2"><circle cx="17" cy="17" r="14"/><path d="M17 8 V17 L23 21"/><circle cx="29" cy="29" r="6" fill="#fff"/><path d="M26 29 L28.5 31.5 L32 27" stroke="#b0131f"/></svg>
  <h3>Reliability</h3>
  <p>Lorem ipsum dolor sit amet, consectetur adipiscing elit, sed do eiusmod tempor incididunt ut</p>
</div>
<div class="abs feature-photo" role="img" aria-label="Person in brown jacket and gloves holding a dark tactical backpack"></div>

<section class="abs reviews">
  <h2>Customer Reviews</h2>
  <span class="rule2"></span>
  <div class="arrow" style="left:111px"><svg width="8" height="12" viewBox="0 0 8 12"><path d="M6 1 L1 6 L6 11" stroke="#fff" stroke-width="2" fill="none"/></svg></div>
  <blockquote>"Lorem ipsum dolor sit amet, consectetur adipiscing elit, sed do eiusmod tempor incididunt ut labore et dolore magna aliqua. Ut enim ad minim veniam, quis nostrud exercitation ullamco laboris nisi ut aliquip ex ea commodo consequat. Duis aute irure dolor in reprehenderit in voluptate velit esse cillum dolore eu fugiat nulla pariatur. Excepteur sint occaecat cupidatat non proident, sunt in culpa qui officia deserunt mollit anim id est laborum."</blockquote>
  <div class="arrow" style="left:1056px"><svg width="8" height="12" viewBox="0 0 8 12"><path d="M2 1 L7 6 L2 11" stroke="#fff" stroke-width="2" fill="none"/></svg></div>
</section>

<h2 class="abs section-title" style="top:2988px">OUR LATEST BLOG</h2>
<div class="abs rule" style="top:3039px"></div>

<div class="abs blog-main" role="img" aria-label="Tactical vest, helmet and gear laid out on a dark surface"></div>
<h3 class="abs blog-main-title">Lorem ipsum dolor sit amet, consectetur adipiscing elit, sed do eiusmod tempor</h3>
<p class="abs blog-main-text">Lorem ipsum dolor sit amet, consectetur adipiscing elit, sed do eiusmod tempor incididunt ut labore et dolore magna aliqua.</p>

<div class="abs blog-thumb" style="top:3071px;background:linear-gradient(135deg,#6a5a48,#2a2622)" role="img" aria-label="Two flashlights on a wooden surface"></div>
<p class="abs blog-item" style="top:3103px">Lorem ipsum dolor sit amet, consectetur adipiscing elit, sed do eiusmod</p>
<div class="abs blog-thumb" style="top:3225px;background:linear-gradient(135deg,#7a7458,#4a4634)" role="img" aria-label="Camouflage pouch with strap"></div>
<p class="abs blog-item" style="top:3257px">Lorem ipsum dolor sit amet, consectetur adipiscing elit, sed do eiusmod</p>
<div class="abs blog-thumb" style="top:3380px;background:linear-gradient(135deg,#8a806a,#5a4a36)" role="img" aria-label="Soldier with a working dog"></div>
<p class="abs blog-item" style="top:3412px">Lorem ipsum dolor sit amet, consectetur adipiscing elit, sed do eiusmod</p>

<footer class="abs footer">
  <div class="fbrand">U.S. TORVANE</div>
  <span class="social" style="left:138px;background:#1f5fb0"></span>
  <span class="social" style="left:190px;background:#1f8fd0"></span>
  <span class="social" style="left:241px;background:#1d5c8c"></span>
  <span class="social" style="left:294px;background:#b0131f"></span>

  <h4 style="left:474px">CONTACT INFO</h4>
  <div class="ci" style="top:110px"><svg width="10" height="13" viewBox="0 0 10 13"><path d="M5 0 A5 5 0 0 1 10 5 C10 8 5 13 5 13 C5 13 0 8 0 5 A5 5 0 0 1 5 0Z" fill="#fff"/><circle cx="5" cy="5" r="1.8" fill="#232323"/></svg><span>Lorem ipsum dolor sit am et, consectetur adip</span></div>
  <div class="ci" style="top:174px"><svg width="12" height="12" viewBox="0 0 12 12"><path d="M2 0 L4.5 3 L3 5 Q5 8 7 9 L9 7.5 L12 10 L10.5 12 Q4 11 0 2 Z" fill="#fff"/></svg><span>+ 1 555 014 2237</span></div>
  <div class="ci" style="top:220px"><svg width="12" height="10" viewBox="0 0 12 10"><rect width="12" height="10" fill="#fff"/><path d="M0 0 L6 5 L12 0" stroke="#232323" fill="none"/></svg><span>info@ustorvane.com</span></div>

  <h4 style="left:804px">NEWSLETTERS</h4>
  <div class="news-input">Enter The Email</div>
  <div class="subscribe">SUBSCRIBE</div>
</footer>
<div class="abs bottom">© Copyrights 2020 &nbsp;U.S. TORVANE &nbsp;| &nbsp;All Rights Reserved</div>

</body>
</html>
```